Can you make a cool and versatile Tarn Meridian Powerpoint template?
See www.tarnmeridian-example.co.uk and http://www.examplenet.invalid/company/tarn-meridian-ltd/ (on the right) to see how the logos are currently used - with interchangeably white and black backgrounds.
Target Market(s)
Marketing managers, product managers in HR technology, HR consultants
Industry/Entity Type
It Company
Font styles to use
Sans Serif
Requirements
Must have
- Master slide design, fonts, color theme, etc. Ideally two variations - one with white background (using colorful logo), one with a darker background (using black/white logo).

```html
<!DOCTYPE html>
<html lang="en">
<head>
<meta charset="utf-8">
<title>Tarn Meridian – Dark Master Slide</title>
<link rel="stylesheet" href="https://fonts.googleapis.com/css2?family=Graduate&family=PT+Sans:wght@400;700&display=swap">
<style>
  :root {
    --page: #ffffff;
    --slide-edge: #0b0b0b;
    --slide-dark: #101112;
    --slide-glow: #3a3b3c;
    --accent-blue: #25a9e1;
    --ink: #1d1d1d;
    --white: #ffffff;
    --sun-hot: #fff6d8;
    --sun-gold: #f2b233;
    --sun-amber: #d9731a;
    --sun-deep: #7a3209;
  }
  * { box-sizing: border-box; margin: 0; padding: 0; }
  html, body {
    width: 1200px; height: 900px; overflow: hidden;
    background: var(--page);
    font-family: "PT Sans", Arial, sans-serif;
  }
  .canvas { position: relative; width: 1200px; height: 900px; }

  .slide {
    position: absolute; left: 21px; top: 182px; width: 1141px; height: 642px;
    background:
      radial-gradient(ellipse 520px 360px at 62% 48%, var(--slide-glow) 0%, rgba(40,40,40,0.35) 45%, transparent 80%),
      var(--slide-dark);
    border: 2px solid var(--slide-edge);
  }

  .photo-frame {
    position: absolute; left: 27px; top: 32px; width: 628px; height: 420px;
    background: var(--white);
  }
  .photo-placeholder {
    position: absolute; left: 12px; top: 9px; width: 605px; height: 403px;
    background:
      radial-gradient(ellipse 260px 140px at 62% 12%, var(--sun-hot) 0%, rgba(255,230,160,0.6) 40%, transparent 75%),
      radial-gradient(ellipse 380px 260px at 55% 60%, var(--sun-gold) 0%, var(--sun-amber) 55%, transparent 100%),
      linear-gradient(180deg, #f5c35a 0%, var(--sun-amber) 45%, var(--sun-deep) 100%);
  }

  .slide-number {
    position: absolute; right: 14px; top: 12px; width: 102px; height: 102px;
  }
  .slide-number svg { display: block; }

  .title-band {
    position: absolute; left: 15px; top: 486px; width: 1109px; height: 142px;
    background: var(--accent-blue);
  }
  .slide-title {
    position: absolute; left: 23px; top: 12px;
    font-family: "Graduate", "Rockwell", serif;
    font-size: 76px; line-height: 1; letter-spacing: -1px;
    color: var(--ink);
    -webkit-text-stroke: 2.5px var(--ink);
    transform: scaleX(0.93); transform-origin: left top;
    white-space: nowrap;
  }
  .title-rule {
    position: absolute; left: 24px; top: 88px; width: 415px; height: 4px;
    background: var(--white);
  }
  .slide-subtitle {
    position: absolute; left: 79px; top: 101px;
    font-size: 19.5px; color: var(--white); letter-spacing: 0.2px;
    white-space: nowrap;
  }
  .contact {
    position: absolute; right: 171px; top: 58px;
    text-align: right; font-size: 11px; line-height: 16px;
    color: var(--white); letter-spacing: 0.1px;
    white-space: nowrap;
  }
  .brand-tile {
    position: absolute; right: 10px; top: 11px; width: 146px; height: 121px;
    background: var(--slide-edge);
    display: flex; align-items: center; justify-content: center; gap: 8px;
  }
  .brand-dot {
    width: 14px; height: 14px; border-radius: 50%; background: var(--accent-blue);
  }
  .brand-name {
    font-size: 17px; font-weight: 700; color: var(--white); white-space: nowrap;
  }
</style>
</head>
<body>
<div class="canvas">
  <section class="slide">
    <div class="photo-frame">
      <div class="photo-placeholder" role="img" aria-label="Photo: person holding a dandelion in a sunlit golden field"></div>
    </div>

    <div class="slide-number">
      <svg width="102" height="102" viewBox="0 0 102 102" aria-label="Slide 02">
        <polygon points="0,0 102,0 102,102" fill="var(--accent-blue)"/>
        <text x="74" y="41" text-anchor="middle" font-family="Graduate, sans-serif" font-size="23" fill="#ffffff" stroke="#ffffff" stroke-width="1.5">02</text>
      </svg>
    </div>

    <div class="title-band">
      <h1 class="slide-title">SLIDE TITLE</h1>
      <div class="title-rule"></div>
      <p class="slide-subtitle">DETAILS OF SLIDE / NAME OF PRESENTOR</p>
      <p class="contact">WWW.SAMPLESITE-DEMO.NET<br>HELLO@SAMPLESITE-DEMO.NET</p>
      <div class="brand-tile">
        <span class="brand-dot"></span>
        <span class="brand-name">Tarn Meridian</span>
      </div>
    </div>
  </section>
</div>
</body>
</html>
```